Realty Group Needs Classy, Contemporary Letterhead Design

We need a letterhead design for a new realty company located in NY, USA. We buy investment properties to rehabilitate and or keep in our rental portfolio.

```html
<!DOCTYPE html>
<html lang="en">
<head>
<meta charset="UTF-8">
<title>Meridian Realty Group – Letterhead</title>
<link href="https://fonts.googleapis.com/css2?family=Montserrat:wght@700&family=Roboto:wght@400&display=swap" rel="stylesheet">
<style>
  :root {
    --backdrop: #e9eaec;
    --paper: #ffffff;
    --brand-purple: #4f3a7c;
    --band-grey: #bcbdc0;
    --watermark-grey: #e7e7e7;
    --on-purple: #ffffff;
  }
  * { margin: 0; padding: 0; box-sizing: border-box; }
  html, body {
    width: 1000px;
    height: 1200px;
    overflow: hidden;
    background: var(--backdrop);
  }
  .canvas {
    position: relative;
    width: 1000px;
    height: 1200px;
  }
  .letterhead {
    position: absolute;
    left: 58px;
    top: 28px;
    width: 804px;
    height: 1040px;
    background: var(--paper);
    transform: scale(1.1);
    transform-origin: top left;
    overflow: hidden;
    font-family: "Roboto", Arial, sans-serif;
  }
  .letterhead__shapes {
    position: absolute;
    inset: 0;
    width: 804px;
    height: 1040px;
  }
  .shape-top { fill: var(--band-grey); }
  .shape-bottom { fill: var(--brand-purple); }

  .brand {
    position: absolute;
    left: 45px;
    top: 72px;
    width: 192px;
    color: var(--brand-purple);
    font-family: "Montserrat", Arial, sans-serif;
    font-weight: 700;
    text-align: center;
  }
  .brand__name {
    display: block;
    font-size: 31px;
    line-height: 34px;
    letter-spacing: -0.3px;
  }
  .brand__tagline {
    display: flex;
    align-items: center;
    gap: 6px;
    font-size: 10px;
    line-height: 12px;
    letter-spacing: 0.6px;
  }
  .brand__tagline::before,
  .brand__tagline::after {
    content: "";
    flex: 1;
    height: 1px;
    background: var(--brand-purple);
  }

  .contact {
    position: absolute;
    color: var(--on-purple);
    font-size: 12px;
    line-height: 14px;
  }
  .contact__item {
    position: absolute;
    display: flex;
    align-items: center;
    gap: 8px;
    white-space: nowrap;
  }
  .contact__icon {
    width: 9px;
    height: 9px;
    fill: var(--on-purple);
    flex: none;
  }
  .contact__item--phone { left: 45px; top: 968px; }
  .contact__item--mobile { left: 45px; top: 995px; }
  .contact__item--email { left: 155px; top: 968px; }
  .contact__item--web { left: 155px; top: 995px; }

  .address {
    position: absolute;
    right: 60px;
    top: 982px;
    display: flex;
    align-items: flex-start;
    gap: 10px;
    color: var(--on-purple);
    font-size: 12px;
    line-height: 15px;
    text-align: right;
  }
  .address__icon {
    width: 13px;
    height: 12px;
    fill: var(--on-purple);
    margin-top: 1px;
  }
</style>
</head>
<body>
<main class="canvas">
  <article class="letterhead">
    <svg class="letterhead__shapes" viewBox="0 0 804 1040" xmlns="http://www.w3.org/2000/svg">
      <defs>
        <radialGradient id="watermark-fill" cx="50%" cy="55%" r="60%">
          <stop offset="0%" stop-color="#e5e5e5"/>
          <stop offset="100%" stop-color="#f2f2f2"/>
        </radialGradient>
      </defs>
      <polygon class="shape-top" points="0,0 804,0 804,3 419,73 489,95 169,12 0,75"/>
      <rect role="img" aria-label="Large faint illustration of an archer drawing a bow, the brand emblem as a watermark"
            x="84" y="465" width="620" height="500" rx="160" fill="url(#watermark-fill)"/>
      <polygon class="shape-bottom" points="0,965 114,908 519,973 376,1020 376,1040 0,1040"/>
      <polygon class="shape-bottom" points="376,1030 671,940 804,987 804,1040 376,1040"/>
    </svg>

    <header class="brand">
      <span class="brand__name">MERIDIAN</span>
      <span class="brand__tagline">Realty Group, LLC</span>
    </header>

    <footer>
      <div class="contact">
        <div class="contact__item contact__item--phone">
          <svg class="contact__icon" viewBox="0 0 10 10"><path d="M2 0.5 L3.6 2.4 L2.8 3.5 C3.4 4.9 4.9 6.4 6.4 7.1 L7.5 6.3 L9.5 7.9 L8.6 9.5 C4.6 9.3 0.7 5.4 0.5 1.4 Z"/></svg>
          <span>00 000 0000</span>
        </div>
        <div class="contact__item contact__item--mobile">
          <svg class="contact__icon" viewBox="0 0 10 10"><path d="M2.5 0 H7.5 V10 H2.5 Z M3.5 1 V8 H6.5 V1 Z"/></svg>
          <span>0000000000</span>
        </div>
        <div class="contact__item contact__item--email">
          <svg class="contact__icon" viewBox="0 0 10 10"><path d="M0 2 H10 V8 H0 Z M0.6 2.4 L5 5.6 L9.4 2.4 L9.4 2.9 L5 6.2 L0.6 2.9 Z" fill-rule="evenodd"/></svg>
          <span>xxxxx@xxxx.xxx</span>
        </div>
        <div class="contact__item contact__item--web">
          <svg class="contact__icon" viewBox="0 0 10 10"><path fill-rule="evenodd" d="M5 0 A5 5 0 1 1 4.99 0 Z M5 1 A4 4 0 1 0 5.01 1 Z M4.6 0.5 H5.4 V9.5 H4.6 Z M0.5 4.6 H9.5 V5.4 H0.5 Z"/></svg>
          <span>xxx.xxxxxxxxxxxxxx.xxx</span>
        </div>
      </div>

      <address class="address" style="font-style: normal;">
        <span>00, xxxxxx, xxxxxxx<br>xxxxxxx-0000</span>
        <svg class="address__icon" viewBox="0 0 13 12"><path d="M6.5 0 L13 6 H11 V12 H8 V8 H5 V12 H2 V6 H0 Z"/></svg>
      </address>
    </footer>
  </article>
</main>
</body>
</html>
```